LM-Steuerberatung WordPress Site fully implemented (tax advisor)

Hello!
I need a little Wordpress Site for my newly founded Tax-Advisor Company.
I am a one-man Office advising in the area of Crypto-Currency.
PLEASE only provide a Design, if you can also Implement a WP-Site afterwards on an existing Webspace.

Please find the Content and Website-Description in the attached Document

Language for the Website is German (for now)

Target Market(s)

Tax-Advisory (specialized in Crypto Currency)

Coding

Coded - Design and coding required

Number of Pages Required

5+ page

Font styles to use
Sans Serif

Requirements
Must have
• Wordpress Implementation afterwards - Details according to attached Project Information Document

```html
<!DOCTYPE html>
<html lang="de">
<head>
<meta charset="utf-8">
<title>LM-Steuerberatung</title>
<link href="https://fonts.googleapis.com/css2?family=Poppins:wght@400;500;600;700;800&display=swap" rel="stylesheet">
<style>
:root{
  --navy:#1b2540;
  --navy-deep:#0e1a36;
  --grey:#8a8a8a;
  --text-grey:#6d6d6d;
  --footer-grey:#7b859c;
  --white:#ffffff;
}
*{margin:0;padding:0;box-sizing:border-box}
html,body{width:1084px;height:1200px;overflow:hidden}
body{font-family:'Poppins',sans-serif;background:var(--white);color:var(--navy);position:relative}
.abs{position:absolute}

.topbar{left:0;top:0;width:1084px;height:40px;background:var(--navy);color:var(--white);font-size:14px}
.social-dot{width:10px;height:10px;border-radius:50%;background:var(--white);top:15px}
.topbar .sep{top:12px;width:2px;height:16px;border-left:2px dotted #5a6480}
.topbar .item{top:10px;display:flex;align-items:center;gap:10px}
.topbar .vline{left:773px;top:10px;width:1px;height:21px;background:#56607a}

.header{left:0;top:40px;width:1084px;height:68px;background:var(--white)}
.brand{display:flex;align-items:center;gap:8px;font-weight:700;letter-spacing:.3px}
.brand-mark{width:18px;height:18px;background:currentColor;border-radius:3px}
.header .brand{left:100px;top:23px;font-size:16px;color:var(--navy)}
.nav{top:27px;font-size:13.5px;font-weight:500;color:#6b7488;text-transform:uppercase}
.nav.active{color:var(--navy)}
.caret{display:inline-block;border:4px solid transparent;border-top:5px solid #6b7488;margin-left:4px;vertical-align:-2px}
.btn-contact{left:857px;top:14px;width:142px;height:40px;border:2px solid var(--navy);border-radius:20px;display:flex;align-items:center;justify-content:center;gap:14px;font-size:13px;font-weight:700;letter-spacing:.8px}

.hero{left:0;top:108px;width:1084px;height:488px;background:linear-gradient(90deg,#f4f6f9 0%,#eef1f5 38%,#c9d2de 58%,#3a475f 78%,#2b3346 100%)}
.hero-tab{left:0;top:108px;width:350px;height:14px;background:var(--white);clip-path:polygon(0 0,100% 0,96% 100%,0 100%)}
.hero .welcome{left:85px;top:162px;font-size:27px;font-weight:700;color:#9a9a9a;letter-spacing:.3px}
.hero h1{left:85px;top:198px;font-size:38px;font-weight:800;color:var(--navy);letter-spacing:.5px}
.hero p{left:85px;top:258px;width:500px;font-size:16px;line-height:29px;color:#2b3246}
.btn-hero{left:85px;top:348px;width:302px;height:48px;border-radius:24px;background:var(--navy);color:var(--white);display:flex;align-items:center;justify-content:center;gap:14px;font-size:13px;font-weight:700;letter-spacing:.2px}
.arrow{top:200px;width:31px;height:82px;background:rgba(150,150,150,.75);display:flex;align-items:center;justify-content:center}

.feature{top:644px;width:270px}
.num{width:53px;height:51px;top:6px;background:var(--grey);border-radius:8px;color:var(--white);font-weight:700;font-size:27px;display:flex;align-items:center;justify-content:center}
.num-line-top{left:36px;top:0;width:27px;height:2px;background:#b9b9b9}
.num-line-bot{left:0;top:62px;width:27px;height:2px;background:#b9b9b9}
.feature p{position:absolute;top:70px;left:0;width:270px;font-size:15px;line-height:29px;color:var(--text-grey)}
.divider{top:644px;width:1px;height:155px;background:#e1e1e1}

.footer{left:0;top:847px;width:1084px;height:353px;background:radial-gradient(ellipse at 70% 40%,#13254a 0%,var(--navy-deep) 70%)}
.footer .brand{left:84px;top:93px;font-size:16px;color:var(--white)}
.footer .about{left:84px;top:139px;width:320px;font-size:15px;line-height:29px;color:var(--footer-grey)}
.footer .copy{left:84px;top:254px;font-size:14px;color:var(--footer-grey)}
.footer h3{top:77px;font-size:17px;font-weight:700;color:var(--white);letter-spacing:.3px}
.links{left:524px;top:114px;list-style:none}
.links li{height:34.3px;font-size:15px;color:var(--footer-grey);display:flex;align-items:center;gap:11px}
.ic-box{width:37px;height:37px;background:#9a9a9a;border-radius:6px;display:flex;align-items:center;justify-content:center}
.c-label{font-size:15px;color:var(--footer-grey);line-height:22px}
.c-value{font-size:16px;color:var(--white);line-height:22px}
.footer .social{left:765px;top:251px;font-size:15px;color:var(--footer-grey);display:flex;align-items:center}
.footer .social span.d{width:10px;height:10px;border-radius:50%;background:var(--white);display:inline-block}
</style>
</head>
<body>

<div class="abs topbar">
  <span class="abs social-dot" style="left:83px"></span>
  <span class="abs sep" style="left:109px"></span>
  <span class="abs social-dot" style="left:131px"></span>
  <span class="abs sep" style="left:161px"></span>
  <span class="abs social-dot" style="left:184px"></span>
  <div class="abs item" style="left:514px">
    <svg width="18" height="16" viewBox="0 0 18 16" fill="none" stroke="#fff" stroke-width="1.4"><path d="M1 7 9 1l8 6v8H1z"/><path d="M1 7l8 5 8-5"/></svg>
    <span>Email: office@lm-steuer.at</span>
  </div>
  <span class="abs vline"></span>
  <div class="abs item" style="left:809px">
    <svg width="18" height="18" viewBox="0 0 18 18" fill="none" stroke="#fff" stroke-width="1.4"><path d="M4 1l3 4-2 2c1 2 3 4 5 5l2-2 4 3-2 3C8 16 2 10 1 4z"/><path d="M11 1a6 6 0 0 1 6 6M11 4a3 3 0 0 1 3 3"/></svg>
    <span>Phone: <b>+43 512 480 271</b></span>
  </div>
</div>

<div class="abs header">
  <div class="abs brand"><span class="brand-mark"></span>LM STEUERBERATUNG</div>
  <span class="abs nav active" style="left:431px">Home</span>
  <span class="abs nav" style="left:504px">Leistungen<span class="caret"></span></span>
  <span class="abs nav" style="left:634px">Über mich</span>
  <span class="abs nav" style="left:747px">Impressum</span>
  <div class="abs btn-contact">KONTAKT
    <svg width="18" height="18" viewBox="0 0 18 18" fill="none" stroke="#1b2540" stroke-width="1.4"><circle cx="9" cy="9" r="8"/><path d="M4 9h9M10 6l3 3-3 3"/></svg>
  </div>
</div>

<section class="abs hero" role="img" aria-label="Foto: zwei Geschäftsmänner im Beratungsgespräch am Laptop, links oben Krypto-Münzen">
  <div class="abs welcome">WILLKOMMEN BEI</div>
  <h1 class="abs">LM-STEUERBERATUNG!</h1>
  <p class="abs">Ihrem Spezialisten bei allen steuerlichen Themen rund um Einkünfte &amp; Vermögen aus Krypto-Assets.</p>
  <div class="abs btn-hero">WEITER ZU UNSEREN LEISTUNGEN <span class="brand-mark" style="width:13px;height:13px;background:#fff"></span></div>
  <div class="abs arrow" style="left:0;border-radius:0 6px 6px 0">
    <svg width="14" height="12" viewBox="0 0 14 12" fill="none" stroke="#fff" stroke-width="1.8"><path d="M13 6H2M6 1 1 6l5 5"/></svg>
  </div>
  <div class="abs arrow" style="left:1053px;border-radius:6px 0 0 6px">
    <svg width="14" height="12" viewBox="0 0 14 12" fill="none" stroke="#fff" stroke-width="1.8"><path d="M1 6h11M8 1l5 5-5 5"/></svg>
  </div>
</section>
<div class="abs hero-tab"></div>

<div class="abs feature" style="left:83px">
  <span class="abs num-line-top"></span><div class="abs num">01</div><span class="abs num-line-bot"></span>
  <p>Dann mach ich eine Schweizer Holding&nbsp; Gesellschaft– dort zahlt man fast keine Steuern</p>
</div>
<span class="abs divider" style="left:374px"></span>
<div class="abs feature" style="left:418px">
  <span class="abs num-line-top"></span><div class="abs num">02</div><span class="abs num-line-bot"></span>
  <p>Dann melde ich einfach meinen Hauptwohnsitz in Österreich ab</p>
</div>
<span class="abs divider" style="left:709px"></span>
<div class="abs feature" style="left:752px">
  <span class="abs num-line-top"></span><div class="abs num">03</div><span class="abs num-line-bot"></span>
  <p>Dann lass ich meine Kryptos auf einer Börse in Singapur, dort ist das steuerfrei</p>
</div>

<footer class="abs footer">
  <div class="abs brand"><span class="brand-mark"></span>LM STEUERBERATUNG</div>
  <p class="abs about">Ihrem Spezialisten bei allen steuerlichen Themen rund um Einkünfte &amp; Vermögen aus Krypto-Assets.</p>
  <div class="abs copy">Copyright © 2022 LM-Steuerberatung</div>

  <h3 class="abs" style="left:524px">QUICK LINKS</h3>
  <ul class="abs links">
    <li><svg width="7" height="10" viewBox="0 0 7 10" fill="none" stroke="#fff" stroke-width="1.8"><path d="M1 1l4 4-4 4"/></svg>Home</li>
    <li><svg width="7" height="10" viewBox="0 0 7 10" fill="none" stroke="#fff" stroke-width="1.8"><path d="M1 1l4 4-4 4"/></svg>Leistungen</li>
    <li><svg width="7" height="10" viewBox="0 0 7 10" fill="none" stroke="#fff" stroke-width="1.8"><path d="M1 1l4 4-4 4"/></svg>Über mich</li>
    <li><svg width="7" height="10" viewBox="0 0 7 10" fill="none" stroke="#fff" stroke-width="1.8"><path d="M1 1l4 4-4 4"/></svg>Impressum</li>
    <li><svg width="7" height="10" viewBox="0 0 7 10" fill="none" stroke="#fff" stroke-width="1.8"><path d="M1 1l4 4-4 4"/></svg>Kontakt</li>
  </ul>

  <h3 class="abs" style="left:765px">CONTACT INFORMATION</h3>
  <div class="abs ic-box" style="left:766px;top:120px">
    <svg width="16" height="14" viewBox="0 0 16 14" fill="#fff"><path d="M0 6 8 0l8 6v8H0z"/></svg>
  </div>
  <div class="abs" style="left:830px;top:114px">
    <div class="c-label">Email:</div>
    <div class="c-value">office@lm-steuer.at</div>
  </div>
  <div class="abs ic-box" style="left:766px;top:184px">
    <svg width="16" height="16" viewBox="0 0 18 18" fill="#fff"><path d="M4 1l3 4-2 2c1 2 3 4 5 5l2-2 4 3-2 3C8 16 2 10 1 4z"/></svg>
  </div>
  <div class="abs" style="left:830px;top:178px">
    <div class="c-label">Phone:</div>
    <div class="c-value">+43 512 480 271</div>
  </div>
  <div class="abs social">Social Media:
    <span class="d" style="margin-left:27px"></span>
    <span class="d" style="margin-left:40px"></span>
    <span class="d" style="margin-left:42px"></span>
  </div>
</footer>

</body>
</html>
```